Business Cards for IT Consulting Company (Managed Service Provider)

I am looking to have some business cards printed and would like some designs. We are an IT Consulting company based in Vancouver BC. I would like a nice clean and modern look to the cards. I have uploaded all the versions of my logo so parts can be used as needed. Here is a snippit from our website homepage:

Quillbrook Networks Ltd. is an IT Solutions Partner located in Vancouver BC, Canada. We offer IT solutions and support to customers in the greater Vancouver Area. With expertise in Microsoft platforms, as well as Linux and Mac OSX and over 12 years experience in the IT industry, Quillbrook Networks is dedicated to offering our clients top quality service and products. We take pride in the solutions we offer our customers. The greatest compliment a client can give us is to recommend our services.

Quillbrook Networks Ltd. offers a wide range of IT services from onsite service to remote support and managed service solutions. This allows clients to choose the support path that best suits their company’s needs. Supporting many different sized companies from small to enterprise level over the past 12 years Quillbrook Networks has the experience and expertise needed to ensure things run smoothly. Allowing our clients to focus on doing business.

Revolutionizing the way IT services are delivered.

Quillbrook Networks is dedicated to providing our clients with IT solutions that work and grow with them for years to come. This philosophy helps save money in the long run instead of replacing equipment constantly. Far too often IT solutions are not well thought out and while possibly solving the problem at hand, require replacement due to growth or quality within a very short time frame. Quillbrook Networks takes pride in providing solutions that will last and be able to accommodate growth without the need for replacement.

Industry/Entity Type

Information Technology

Contact Information for Business Card

Quillbrook Networks Ltd.
(Employee Name)
Eml: (Employees Email Address)
Web: quillbrook.me
Ph: 604-555-0148

Font styles to use
Serif
Sans Serif

Requirements
Must have
• The Company logo and company colors.
Nice to have
• - Our tag line: "Revolutionizing IT Services" or "Revolutionizing the way IT services are delivered."
• - Also I really like the idea of nature and technology together blending which is sort of where my logo came from so integrating that somehow onto the business cards would be great.

```html
<!DOCTYPE html>
<html lang="en">
<head>
<meta charset="utf-8">
<title>Quillbrook Networks Ltd. – Business Card</title>
<link rel="stylesheet" href="https://fonts.googleapis.com/css2?family=Source+Sans+3:wght@400;500&display=swap">
<style>
  :root {
    --page-bg: #d9d6d2;
    --card-bg: #eef1f3;
    --brand-blue: #1a8fd8;
    --panel-blue: #1683cf;
    --panel-light: #e9f4fc;
    --panel-soft: #cfe6f7;
  }
  html, body {
    margin: 0;
    padding: 0;
    width: 1200px;
    height: 969px;
    overflow: hidden;
    background: var(--page-bg);
  }
  .canvas {
    position: relative;
    width: 1200px;
    height: 969px;
  }
  .card {
    position: absolute;
    left: 100px;
    top: 199px;
    width: 1000px;
    height: 571px;
    background: var(--card-bg);
    box-shadow: 0 10px 30px rgba(0,0,0,0.12);
    overflow: hidden;
    font-family: "Source Sans 3", sans-serif;
  }
  .card-panel {
    position: absolute;
    inset: 0;
  }
  .brand {
    position: absolute;
    left: 85px;
    top: 88px;
    color: var(--brand-blue);
    font-weight: 500;
    line-height: 1;
  }
  .brand-name {
    display: block;
    font-size: 66px;
    letter-spacing: 0.5px;
  }
  .brand-suffix {
    display: block;
    font-size: 24px;
    letter-spacing: 2px;
    margin-top: 6px;
    margin-left: 3px;
  }
  .contact {
    position: absolute;
    right: 45px;
    top: 264px;
    text-align: right;
    color: var(--panel-soft);
  }
  .contact-name {
    margin: 0 0 20px;
    font-size: 40px;
    font-weight: 500;
    color: var(--panel-light);
    line-height: 1;
  }
  .contact-address {
    margin: 0 0 14px;
    font-size: 26px;
    line-height: 36px;
    font-style: normal;
  }
  .contact-list {
    list-style: none;
    margin: 0;
    padding: 0;
    font-size: 25px;
    line-height: 38px;
  }
  .contact-list li {
    display: flex;
    justify-content: flex-end;
    align-items: center;
    gap: 14px;
  }
  .contact-icon {
    width: 22px;
    height: 22px;
    fill: var(--panel-light);
  }
</style>
</head>
<body>
<main class="canvas">
  <section class="card" aria-label="Quillbrook Networks business card">
    <svg class="card-panel" width="1000" height="571" viewBox="0 0 1000 571" aria-hidden="true">
      <defs>
        <linearGradient id="panelShade" x1="0" y1="0" x2="1" y2="1">
          <stop offset="0" stop-color="#1a8ad6"/>
          <stop offset="1" stop-color="#0f6fbd"/>
        </linearGradient>
      </defs>
      <polygon points="678,204 968,204 1000,256 1000,571 611,571 544,446" fill="url(#panelShade)"/>
    </svg>

    <div class="brand">
      <span class="brand-name">Quillbrook</span>
      <span class="brand-suffix">NETWORKS LTD.</span>
    </div>

    <div class="contact">
      <h1 class="contact-name">Daniel Hartley</h1>
      <address class="contact-address">2146 Larkspur Crescent<br>Burnaby, BC V5H 2K9</address>
      <ul class="contact-list">
        <li>604-555-0148
          <svg class="contact-icon" viewBox="0 0 24 24" aria-hidden="true"><path d="M6.6 10.8a15.1 15.1 0 0 0 6.6 6.6l2.2-2.2a1 1 0 0 1 1-.25 11.4 11.4 0 0 0 3.6.57 1 1 0 0 1 1 1V20a1 1 0 0 1-1 1A17 17 0 0 1 3 4a1 1 0 0 1 1-1h3.5a1 1 0 0 1 1 1c0 1.25.2 2.45.57 3.6a1 1 0 0 1-.25 1z"/></svg>
        </li>
        <li>dhartley@quillbrook.me
          <svg class="contact-icon" viewBox="0 0 24 24" aria-hidden="true"><path d="M2 5h20v14H2z M3.5 6.5 12 13l8.5-6.5" fill="none" stroke="#e9f4fc" stroke-width="0"/><path d="M2 5h20v2l-10 6.5L2 7z"/><path d="M2 9l10 6.5L22 9v10H2z"/></svg>
        </li>
        <li>www.quillbrook.me
          <svg class="contact-icon" viewBox="0 0 24 24" aria-hidden="true"><circle cx="12" cy="12" r="10" fill="none" stroke="#e9f4fc" stroke-width="2"/><path d="M2 12h20M12 2c3 3 3 17 0 20M12 2c-3 3-3 17 0 20" fill="none" stroke="#e9f4fc" stroke-width="1.6"/></svg>
        </li>
      </ul>
    </div>
  </section>
</main>
</body>
</html>
```